Clean Modern Skin Product branding/ label.

I need a label for a skincare line. The company is Dermaloft but product names will vary. A couple products to list are:
Sensitive Cleanser, Lumeno, Repair, Halo up, Mendora, Mendora Plus, Mendora Intense, Tavelo, Balance and Vivanto.

I would like the color scheme to be muted greens, grays, tourquise. The bottles are white, boston shaped with pumps, and ounces are 2, 4, 8, 16 ounces. When I choose the design, I can give you exact label sizes. Along with the ingredience already on the product label.

The look I desire is clean, minimal. A modern, organic look. Ideas that come to mind are a Veloraine,https://www.veloraine-example.com/product/2846/37204/3-step/step-2-exfoliate/clarifying-lotion-1 and the simplicity of Bo Tarn.

Both styles high light the name, in this case Dermaloft, and then the specific product.

My product is clean utilizing pure ingredients rather that a bunch fillers and binders. When I work with my clients I normally will say we need to "restore the balance" from over use of harsh products. That is why this lines works. It restores the skin to it's natural state. The process is simple, so I would like the label to reflect that simplicity.

Target Market(s)

Anyone with sensitive skin. So gender neutral

Industry/Entity Type

Skin Care Product

Font styles to use
Serif
Sans Serif
Decorative

Colors
acd037
33b8a4
fcfefd
85cae6
d3d3d3

Requirements
Must have
• Logo, name of product and color identity for cleanser, Active products, moisturizers
• I am thinking we could have one color for a cleanser and a space where I can put a sticker on which cleanser it is. Acne Cleasner, Sensitive Cleanser, and Cleanser.
Nice to have
• Not sure....suprise me. I would like the font to stay the same on the DERMALOFT, but you can change color, or color of leaf.
Should not have
• Too busy, too crowded or look like every other skincare line

```html
<!DOCTYPE html>
<html lang="en">
<head>
<meta charset="UTF-8">
<title>Dermaloft — Mendora Intense Label</title>
<link href="https://fonts.googleapis.com/css2?family=League+Spartan:wght@700&family=Raleway:wght@400&family=Tinos&display=swap" rel="stylesheet">
<style>
  :root {
    --lavender: #cbcde0;
    --mist: #d4d6e4;
    --aqua: #a9e0d2;
    --mint: #bfe6da;
    --white: #fcfefd;
  }
  * { margin: 0; padding: 0; box-sizing: border-box; }
  html, body { width: 876px; height: 1200px; overflow: hidden; }
  body { background: var(--lavender); }
  .label {
    position: relative;
    width: 876px;
    height: 1200px;
    overflow: hidden;
    color: var(--white);
  }
  .label__backdrop {
    position: absolute;
    inset: 0;
    background:
      radial-gradient(ellipse 520px 260px at 80% 20%, rgba(169,224,210,0.7), transparent 70%),
      radial-gradient(ellipse 600px 300px at 15% 75%, rgba(169,224,210,0.75), transparent 70%),
      radial-gradient(ellipse 500px 260px at 85% 95%, rgba(191,230,218,0.8), transparent 70%),
      linear-gradient(155deg, var(--mist) 0%, var(--aqua) 35%, var(--lavender) 55%, var(--mint) 80%, var(--lavender) 100%);
  }
  .label__content {
    position: absolute;
    left: 196px;
    top: 0;
    width: 560px;
  }
  .brand-name {
    position: absolute;
    top: 134px;
    font-family: "League Spartan", sans-serif;
    font-weight: 700;
    font-size: 64px;
    letter-spacing: -1px;
    line-height: 1;
  }
  .product-name {
    position: absolute;
    top: 292px;
    font-family: "League Spartan", sans-serif;
    font-weight: 700;
    font-size: 86px;
    line-height: 93px;
    letter-spacing: -0.5px;
    white-space: nowrap;
  }
  .tagline {
    position: absolute;
    top: 552px;
    font-family: "Raleway", sans-serif;
    font-size: 27px;
    letter-spacing: 0.3px;
    white-space: nowrap;
  }
  .description {
    position: absolute;
    top: 594px;
    width: 560px;
    font-family: "Tinos", serif;
    font-size: 29.5px;
    line-height: 39.5px;
    white-space: nowrap;
  }
  .volume {
    position: absolute;
    top: 1002px;
    font-family: "League Spartan", sans-serif;
    font-weight: 700;
    font-size: 28px;
    letter-spacing: 0.5px;
    white-space: nowrap;
  }
</style>
</head>
<body>
  <main class="label">
    <div class="label__backdrop" role="img" aria-label="Soft marbled swirls of aqua and lavender"></div>
    <div class="label__content">
      <div class="brand-name">Dermaloft</div>
      <h1 class="product-name">Mendora<br>Intense.</h1>
      <p class="tagline">RESTORE THE BALANCE</p>
      <p class="description">
        Lilutpat ut wisi eniml orem ipsum<br>
        dolor sit amet, consectetuer<br>
        adipiscing elit, sed diam nonummy<br>
        nibh euismod tincidunt ut laoreet<br>
        dolore magna aliquam erat volutpat.<br>
        Ut wisi enim ad minim veniam, quis<br>
        nostrud exerci tation ullamcorper<br>
        suscipit lobortis nisl ut aliquip ex ea<br>
        commodo consequat.
      </p>
      <p class="volume">16FL.OZ — 500ML</p>
    </div>
  </main>
</body>
</html>
```